Business Card Design

We have recently seen two business cards that caught our attention and think the designs would work for us. We are an accounting firm that serves small businesses in a variety of industries. Attached are the two business card that inspired us along with very rough layouts. We would like to see a professional layout using our company information.

Industry/Entity Type

Accounting

Contact Information for Business Card

Company Name - Marlowe Thistle
Address - 4182 Orlanby Lane, Suite 610, Houston, TX 77093
713-555-0187 - Main
281-555-0342 - Fax

Team Member Names, emails and phone numbers (see attachment)

```html
<!DOCTYPE html>
<html lang="en">
<head>
<meta charset="utf-8">
<title>Marlowe Thistle – Business Card</title>
<link rel="stylesheet" href="https://fonts.googleapis.com/css2?family=Lato:wght@400;700;900&display=swap">
<style>
  :root {
    --backdrop: #e9e9e9;
    --card: #ffffff;
    --ink: #111111;
    --ink-soft: #3a3a3a;
    --muted: #8c8c8c;
    --rule: #a9a9a9;
    --band: #c9c9c9;
    --mark: #b5b5b5;
  }
  * { box-sizing: border-box; margin: 0; padding: 0; }
  html, body {
    width: 1200px; height: 527px; overflow: hidden;
    background: var(--backdrop);
    font-family: "Lato", Arial, sans-serif;
    color: var(--ink);
  }
  .card {
    position: absolute; left: 210px; top: 40px;
    width: 780px; height: 446px;
    background: var(--card);
    box-shadow: 0 6px 18px rgba(0,0,0,0.18);
    overflow: hidden;
  }
  .brand {
    position: absolute; left: 62px; top: 122px;
    display: flex; align-items: center; gap: 12px;
  }
  .brand-square { width: 18px; height: 18px; background: var(--mark); }
  .brand-name {
    font-weight: 900; font-size: 30px; letter-spacing: 0.5px; color: var(--ink);
  }
  .divider {
    position: absolute; left: 400px; top: 64px;
    width: 2px; height: 150px; background: var(--rule);
  }
  .member {
    position: absolute; right: 56px; top: 64px;
    text-align: right;
  }
  .member-name {
    font-weight: 900; font-size: 22px; color: var(--ink-soft); letter-spacing: 0.3px;
  }
  .member-role { font-size: 13px; color: var(--muted); margin-bottom: 8px; }
  .contact-line {
    display: flex; justify-content: flex-end; align-items: center; gap: 7px;
    font-size: 17px; line-height: 26px; color: var(--ink);
  }
  .icon { width: 15px; height: 15px; flex: none; }
  .company {
    position: absolute; left: 190px; top: 252px;
  }
  .company-name {
    font-weight: 900; font-size: 36px; letter-spacing: 0.6px; line-height: 42px;
  }
  .company-address { font-size: 17px; line-height: 26px; }
  .company-phones {
    display: flex; gap: 60px; font-size: 17px; line-height: 26px;
  }
  .company-phones span { display: flex; align-items: center; gap: 8px; }
  .band {
    position: absolute; left: 0; bottom: 0; width: 100%; height: 54px;
    background: var(--band);
  }
  .website {
    position: absolute; left: 300px; top: 8px;
    font-weight: 700; font-size: 16px; color: var(--ink-soft);
  }
</style>
</head>
<body>
  <article class="card">
    <div class="brand">
      <span class="brand-square"></span>
      <span class="brand-name">Marlowe Thistle</span>
    </div>

    <div class="divider"></div>

    <section class="member">
      <h2 class="member-name">DELPHINE ARCHER</h2>
      <p class="member-role">Account Manager</p>
      <p class="contact-line">
        <svg class="icon" viewBox="0 0 16 16"><path d="M2 5c0-2 2-3 6-3s6 1 6 3v1h-3V5H5v1H2z M3 8h10l1 6H2z" fill="currentColor"/></svg>
        713-555-0187
      </p>
      <p class="contact-line">
        <svg class="icon" viewBox="0 0 16 16"><rect x="4" y="1" width="8" height="14" rx="1.5" fill="none" stroke="currentColor" stroke-width="1.5"/></svg>
        832-555-0129
      </p>
      <p class="contact-line">
        <svg class="icon" viewBox="0 0 16 16"><rect x="1" y="3" width="14" height="10" fill="currentColor"/><path d="M1 3l7 6 7-6" fill="none" stroke="#fff" stroke-width="1.3"/></svg>
        darcher@marlowethistle.com
      </p>
    </section>

    <section class="company">
      <h1 class="company-name">MARLOWE THISTLE</h1>
      <p class="company-address">4182 Orlanby Lane, Suite 610, Houston, TX 77093</p>
      <p class="company-phones">
        <span>
          <svg class="icon" viewBox="0 0 16 16"><path d="M2 5c0-2 2-3 6-3s6 1 6 3v1h-3V5H5v1H2z M3 8h10l1 6H2z" fill="currentColor"/></svg>
          713-555-0187
        </span>
        <span>
          <svg class="icon" viewBox="0 0 16 16"><rect x="4" y="1" width="8" height="4" fill="currentColor"/><rect x="1" y="6" width="14" height="6" rx="1" fill="currentColor"/><rect x="4" y="10" width="8" height="5" fill="#fff" stroke="currentColor" stroke-width="1.2"/></svg>
          281-555-0342
        </span>
      </p>
    </section>

    <footer class="band">
      <span class="website">www.marlowethistle.com</span>
    </footer>
  </article>
</body>
</html>
```